Stonebridge Building and Projects business cards

A business card with watermark background (construction work)

Company logo attached

Home improvement projects
House renovations
Bathroom and kitchen renovations
House extensions
New builds and granny flats

Director Omar Haddani
(Phone number)
omar@sbpbuilding.com.au
(Instagram logo) sbp_building

```html
<!DOCTYPE html>
<html lang="en">
<head>
<meta charset="utf-8">
<title>Stonebridge Building and Projects — Business Cards</title>
<link href="https://fonts.googleapis.com/css2?family=Montserrat:wght@600&family=Roboto:wght@400&family=Fira+Sans:wght@400;600&family=Arvo&display=swap" rel="stylesheet">
<style>
  :root {
    --backdrop: #2b2b2b;
    --card-dark: #0e1012;
    --card-dark-2: #1a1d20;
    --brand-blue: #0a74bd;
    --shade: #3b3e42;
    --white: #ffffff;
    --paper: #f8f8f8;
    --ink: #2c2c2c;
  }
  * { box-sizing: border-box; margin: 0; padding: 0; }
  html, body { width: 1138px; height: 1200px; overflow: hidden; }
  body { background: var(--backdrop); position: relative; font-family: "Roboto", sans-serif; }

  .card {
    position: absolute; top: 288px; width: 376px; height: 622px;
    border-radius: 16px; overflow: hidden;
  }
  .card--front { left: 166px; background: var(--card-dark); color: var(--white); }
  .card--back { left: 600px; background: var(--paper); color: var(--ink); }

  .watermark {
    position: absolute; inset: 0 0 46px 0;
    background: radial-gradient(ellipse at 60% 35%, var(--card-dark-2), var(--card-dark) 70%);
  }

  .brand {
    position: absolute; left: 0; right: 0; text-align: center;
    font-family: "Montserrat", sans-serif; font-weight: 600; color: var(--white);
  }
  .brand__mark {
    display: block; width: 22px; height: 22px; margin: 0 auto 14px;
    background: var(--white);
  }
  .brand__name { font-size: 30px; line-height: 1.15; }
  .brand__sub { font-size: 20px; line-height: 1.3; }

  .tagline {
    position: absolute; left: 0; right: 0; text-align: center;
    font-family: "Arvo", serif; font-size: 20px;
  }
  .tagline span { display: inline-block; padding: 0 4px 1px; border-bottom: 2px solid currentColor; }
  .card--front .tagline { top: 272px; color: var(--brand-blue); }

  .services { position: absolute; top: 366px; left: 0; right: 0; list-style: none; text-align: center; font-size: 16px; }
  .services li { height: 32px; line-height: 26px; }
  .services .ruled span { display: inline-block; padding: 0 12px; border-bottom: 1.5px solid var(--brand-blue); }
  .services .divider { color: var(--brand-blue); margin: 0 8px; }

  .social {
    position: absolute; left: 0; right: 0; text-align: center; font-size: 16px;
    display: flex; justify-content: center; align-items: center; gap: 10px;
  }
  .social__dot { width: 14px; height: 14px; border: 2px solid #c13584; border-radius: 50%; }
  .card--front .social { top: 518px; }

  .footer-band {
    position: absolute; left: 0; right: 0; bottom: 0; height: 46px;
    background: var(--brand-blue); text-align: center; line-height: 46px; font-size: 16px;
  }

  .header-wave { position: absolute; top: 0; left: 0; width: 376px; height: 300px; }
  .card--back .brand { top: 52px; }
  .card--back .tagline { top: 216px; color: var(--white); }

  .person { position: absolute; top: 342px; left: 0; right: 0; text-align: center; font-family: "Fira Sans", sans-serif; }
  .person__name { font-weight: 600; font-size: 26px; color: var(--brand-blue); }
  .person__role { font-size: 16px; margin-top: 2px; }

  .contact-icons { position: absolute; top: 424px; left: 0; width: 376px; height: 28px; }

  .contact { position: absolute; top: 464px; left: 0; right: 0; text-align: center; font-size: 17px; line-height: 24px; list-style: none; }
  .contact .accent { color: var(--brand-blue); }
  .card--back .social { top: 554px; font-size: 17px; }
</style>
</head>
<body>

<section class="card card--front">
  <div class="watermark" role="img" aria-label="Faint construction site building photo watermark"></div>

  <div class="brand" style="top:92px">
    <span class="brand__mark"></span>
    <div class="brand__name">Stonebridge</div>
    <div class="brand__sub">Building and Projects</div>
  </div>

  <p class="tagline"><span>Built to last!</span></p>

  <ul class="services">
    <li class="ruled"><span>Home Improvement Projects</span></li>
    <li class="ruled"><span>Bathroom &amp; Kitchen Renovations</span></li>
    <li class="ruled"><span>New Builds &amp; Granny Flats</span></li>
    <li>House Renovations<span class="divider">|</span>House Extensions</li>
  </ul>

  <p class="social"><span class="social__dot"></span>sbp_building</p>

  <div class="footer-band">www.sbpbuilding.com.au</div>
</section>

<section class="card card--back">
  <svg class="header-wave" viewBox="0 0 376 300" aria-hidden="true">
    <path d="M0 0 H376 V222 C300 300 140 300 0 250 Z" fill="var(--shade)" transform="translate(0 8)"/>
    <path d="M0 0 H376 V214 C300 290 140 292 0 246 Z" fill="var(--brand-blue)"/>
  </svg>

  <div class="brand">
    <span class="brand__mark"></span>
    <div class="brand__name">Stonebridge</div>
    <div class="brand__sub">Building and Projects</div>
  </div>

  <p class="tagline"><span>Built to last!</span></p>

  <div class="person">
    <div class="person__name">Omar Haddani</div>
    <div class="person__role">Managing Director</div>
  </div>

  <svg class="contact-icons" viewBox="0 0 376 28" aria-hidden="true">
    <path d="M84 14 L134 12.5 L134 15.5 Z" fill="var(--ink)"/>
    <path d="M292 14 L242 12.5 L242 15.5 Z" fill="var(--ink)"/>
    <g fill="none" stroke="var(--brand-blue)" stroke-width="1.6">
      <circle cx="160" cy="14" r="12"/>
      <circle cx="188" cy="14" r="12"/>
      <circle cx="216" cy="14" r="12"/>
    </g>
    <circle cx="160" cy="14" r="9" fill="var(--brand-blue)"/>
    <circle cx="188" cy="14" r="9" fill="var(--brand-blue)"/>
    <circle cx="216" cy="14" r="9" fill="var(--brand-blue)"/>
    <path d="M155 17 h10 v-3 q-5 -4 -10 0 Z" fill="var(--white)"/>
    <rect x="183" y="10" width="10" height="8" fill="none" stroke="var(--white)" stroke-width="1.2"/>
    <path d="M183 10 L188 15 L193 10" fill="none" stroke="var(--white)" stroke-width="1.2"/>
    <g fill="none" stroke="var(--white)" stroke-width="1">
      <circle cx="216" cy="14" r="5.5"/>
      <ellipse cx="216" cy="14" rx="2.2" ry="5.5"/>
      <path d="M210.5 14 h11"/>
    </g>
  </svg>

  <ul class="contact">
    <li>0412 555 318</li>
    <li>omar@sbpbuilding.com.au</li>
    <li>www.<span class="accent">sbpbuilding</span>.com.au</li>
  </ul>

  <p class="social"><span class="social__dot"></span>sbp_building</p>
</section>

</body>
</html>
```